Bluefern Business Services needs a new interactive and interesting website

We need an interesting, professional, modern and functional company website for Bluefern Business Services - a young IT Services company based out of Chennai, India.

Bluefern Business Services is a fully owned subsidiary of Marlow Goods, one of the world's leading direct to consumer wine merchant.

We already have a registered company logo which must feature in the website.

We conceive, design, develop, test, implement and support IT solutions across the entire Marlow Goods IT landscape. For ex : We currently run about 25 e-commerce websites for Marlow Goods on ATG and Dot Net.

We would like to see our corporate colors used in the website. (Burgundy wine and wine green - source: www.bluefernbs-site.com)

We are looking at this website to communicate a fun, friendly and professionally managed company - reaching out to career seekers, prospective customers and general public.

For reference - The company name 'Bluefern' is an inspiration from the Marlow Goods lineage.

The second image with the world map is stickered on our main entrance to the office, I am not sure where this can be used -just putting it out there..

Please note that there are only a few more days to submit designs for this contest  !

I would appreciate if you can help posting your designs in time for our review and consideration.

Thanks.

Reason: Thanks for your inputs. We have a number of designers and a lot to digest and work with in the past few days. There has been a rush of new designs in the last few days Hence we will require more time to process these and make our decision. Hence i am requesting the contest to be open for more days. Regards, Tarun

Target Market(s)

Prospective job seekers who want to know more about the company and also wish to apply for a job vacancy
People wanting to know more about the company in general and our progress
People who want to see what we offer and how we can help them too - prospective customers
Companies that are interested in our IT Captive journey and are looking for a business opportunity

Industry/Entity Type

E-Commerce

Requirements
Must have
• Log In/ Register facility acting as a Single Sign on for Intranet (Employees)

Facility to post job vacancies (with an expiry date) and enable people to apply for a role and upload their CV/Resume.

Facility to Review Job applications

Facility for website visitors to contact Bluefern business Services via an online 'Contact Us' form with a split of job seekers and business opportunities

Gallery facility to upload pictures regarding company events
Nice to have
• Less Cluttered and contemporary design
Some Wine/Vineyard inspirations will be good but not too much, the company is an IT services company

```html
<!DOCTYPE html>
<html lang="en">
<head>
<meta charset="utf-8">
<title>Bluefern Business Services</title>
<link rel="stylesheet" href="https://fonts.googleapis.com/css2?family=PT+Sans:ital,wght@0,400;0,700;1,400&display=swap">
<style>
:root{
  --burgundy:#a0124f;
  --burgundy-dark:#7d0d3c;
  --burgundy-deep:#8c1048;
  --wine-green:#a8c93a;
  --green-light:#c6dd63;
  --text:#3a3a3a;
  --muted:#777;
  --grey-band:#e6e6e6;
  --date-grey:#757372;
  --white:#fff;
}
*{box-sizing:border-box;margin:0;padding:0}
html,body{width:993px;height:1200px;overflow:hidden}
body{position:relative;font-family:"PT Sans",Arial,sans-serif;color:var(--text);background:#cfc8b4}
.backdrop{position:absolute;inset:0;background:
  radial-gradient(ellipse 160px 260px at 930px 860px,rgba(230,190,60,.55),transparent 70%),
  radial-gradient(ellipse 140px 300px at 40px 950px,rgba(120,110,60,.45),transparent 70%),
  linear-gradient(180deg,#e8e3d6 0%,#d9d3c0 45%,#b6ab7c 75%,#8a7a3a 90%,#5d5326 100%)}
.header{position:absolute;left:0;top:0;width:993px;height:100px;
  background:linear-gradient(90deg,#8a0f44 0%,#b51d62 30%,#a0124f 60%,#7d0d3c 100%)}
.brand{position:absolute;left:106px;top:26px;color:var(--white);font-size:30px;line-height:1;font-weight:700}
.brand-mark{display:inline-block;width:22px;height:22px;border-radius:50%;background:var(--white);vertical-align:middle;margin-right:6px}
.brand small{display:block;font-size:19px;font-weight:700;margin:4px 0 0 30px}
.notice{position:absolute;left:508px;top:31px;width:409px;height:50px;background:rgba(110,8,50,.85);
  border-radius:3px;color:var(--white);font-size:10.5px;line-height:20px;padding:5px 0 0 12px}
.notice::after{content:"";position:absolute;left:28px;bottom:-8px;border:8px solid transparent;border-bottom:0;border-top-color:rgba(110,8,50,.85)}
.hero{position:absolute;left:0;top:100px;width:993px;height:425px;overflow:hidden;
  background:
  radial-gradient(ellipse 150px 200px at 20px 60px,rgba(120,175,40,.85),transparent 70%),
  radial-gradient(ellipse 70px 260px at 0px 230px,rgba(140,190,60,.7),transparent 70%),
  radial-gradient(ellipse 230px 240px at 860px 170px,rgba(130,125,160,.75),transparent 70%),
  radial-gradient(ellipse 120px 130px at 380px 120px,rgba(225,185,150,.75),transparent 72%),
  radial-gradient(ellipse 120px 130px at 540px 140px,rgba(215,175,140,.7),transparent 72%),
  radial-gradient(ellipse 260px 190px at 470px 300px,rgba(205,208,225,.95),transparent 72%),
  radial-gradient(ellipse 120px 120px at 330px 40px,rgba(90,70,55,.55),transparent 70%),
  radial-gradient(ellipse 110px 110px at 550px 40px,rgba(150,110,70,.5),transparent 70%),
  linear-gradient(90deg,#f2f7ea 0%,#f7f7f4 14%,#e6e3e6 40%,#d7d6df 65%,#bfc0d0 100%)}
.hero svg{position:absolute;left:0;bottom:0}
.nav{position:absolute;left:97px;top:100px;width:817px;height:35px;background:var(--green-light);display:flex;align-items:center;z-index:2}
.nav a{color:var(--white);text-decoration:none;font-size:16px;padding:0 15px;height:35px;line-height:35px}
.nav a.active{background:var(--burgundy)}
.search{position:absolute;right:12px;top:5px;width:143px;height:25px;background:var(--white);border-radius:3px;font-size:10px;font-style:italic;color:#999;padding:6px 9px}
.search svg{position:absolute;right:6px;top:4px}
.slide-arrow{position:absolute;top:315px;width:26px;height:26px;border-radius:50%;background:#f1f1f1;border:2px solid #ddd;z-index:2}
.slide-arrow svg{position:absolute;left:7px;top:6px}
.event{position:absolute;left:104px;top:401px;width:788px;height:116px;background:var(--burgundy-deep);border-radius:3px;z-index:2}
.event-label{position:absolute;left:0;top:0;width:164px;height:116px;background:linear-gradient(180deg,#2c2c2c,#121212);color:var(--white);font-style:italic;text-align:right;padding:42px 12px 0 0}
.event-label strong{display:block;font-weight:400;font-size:22px}
.event-label span{font-size:12px}
.event-text{position:absolute;left:180px;top:20px;width:470px;color:var(--white);font-style:italic;font-size:11.5px;line-height:20px}
.event-video{position:absolute;left:660px;top:10px;width:119px;height:97px;background:linear-gradient(135deg,#c6c9cf,#8e949f 60%,#6c717b)}
.event-video svg{position:absolute;left:38px;top:27px}
.card{position:absolute;left:82px;top:525px;width:831px;height:627px;background:var(--white);border-radius:0 0 12px 12px}
.welcome{position:absolute;left:14px;top:16px;width:803px;text-align:center}
.welcome h1{font-weight:400;font-size:19px;color:var(--burgundy);display:flex;align-items:center;gap:10px}
.welcome h1::before,.welcome h1::after{content:"";flex:1;height:1px;background:#ddd}
.tagline{color:var(--wine-green);font-weight:700;font-style:italic;font-size:13px;margin-top:8px}
.welcome p{font-size:12px;line-height:20px;margin:2px 36px 0}
.btn{display:inline-block;background:var(--burgundy);color:var(--green-light);border-radius:14px;text-decoration:none}
.btn-large{font-size:13px;padding:4px 13px;margin-top:10px}
.services{position:absolute;left:36px;top:158px;width:390px}
.section-title{font-weight:400;font-size:18px;color:var(--burgundy)}
.service-list{list-style:none;display:grid;grid-template-columns:146px 240px;row-gap:13px;margin-top:17px;margin-left:-2px}
.service-list li{font-size:12.5px;color:var(--burgundy);display:flex;align-items:center;gap:5px}
.services p{font-size:11.5px;line-height:20px;margin-top:14px}
.btn-small{font-size:9px;padding:2px 10px;margin-top:6px}
.divider{position:absolute;left:423px;top:162px;width:1px;height:260px;background:#ddd}
.opportunities{position:absolute;left:475px;top:156px;width:340px}
.job{position:relative;height:85px;margin-top:16px}
.job+.job{margin-top:0}
.date{position:absolute;top:0;width:75px;height:75px;border-radius:50%;background:var(--date-grey);color:var(--white);text-align:center;font-size:19px;line-height:22px;padding-top:15px}
.job-info{position:absolute;top:10px;font-size:10.5px;line-height:13px;width:210px}
.job-info b{font-weight:400;color:#333}
.job-info p{color:var(--muted);margin-top:10px}
.job-info a{color:var(--burgundy);text-decoration:none}
.clients{position:absolute;left:0;top:423px;width:831px;height:98px;background:var(--grey-band);border-bottom:3px solid #ccc;display:flex;align-items:center;padding-left:23px}
.clients-title{display:flex;align-items:flex-end;gap:10px;font-size:12px;color:#333;width:160px}
.client{font-size:13px;color:#555;text-align:center;width:126px;display:flex;align-items:center;justify-content:center;gap:5px}
.client i{display:inline-block;width:8px;height:8px;background:var(--burgundy)}
.footer-nav{position:absolute;left:0;top:551px;width:831px;text-align:center}
.footer-nav a{color:var(--burgundy);text-decoration:none;font-size:15px;margin:0 12px}
.copyright{position:absolute;left:0;top:593px;width:831px;text-align:center;font-size:10.5px;color:#444}
.version{position:absolute;right:36px;top:606px;font-size:10px;color:#222}
.social{position:absolute;left:443px;top:1160px;display:flex;gap:6px}
.social span{width:25px;height:25px;border-radius:3px;background:#3f6fb6}
.social span:nth-child(2){background:#3aa0c9}
.social span:nth-child(3){background:#e87c1f}
</style>
</head>
<body>
<div class="backdrop" role="img" aria-label="Soft-focus vineyard rows in autumn light"></div>

<header class="header">
  <div class="brand"><span class="brand-mark"></span>bluefern<small>Business Services</small></div>
  <div class="notice">Current Opportunities : There are often a number of opportunities available at Bluefern.<br>Here are the latest ones. Be sure to get your application form in before the closing date!</div>
</header>

<section class="hero" role="img" aria-label="Three colleagues smiling around a tablet, with vine leaves at the left and grape clusters at the right">
  <svg width="993" height="150" viewBox="0 0 993 150">
    <defs>
      <linearGradient id="hero-grass" x1="0" y1="0" x2="0" y2="1">
        <stop offset="0" stop-color="#c4d66c"/><stop offset="1" stop-color="#8ea432"/>
      </linearGradient>
    </defs>
    <path d="M0 118 Q520 128 993 20 L993 150 L0 150Z" fill="url(#hero-grass)"/>
    <path d="M0 116 Q520 126 993 18" fill="none" stroke="#f4f4ec" stroke-width="3"/>
  </svg>
</section>

<nav class="nav">
  <a class="active" href="#">Home</a><a href="#">About Us</a><a href="#">Clients</a><a href="#">Services</a><a href="#">Careers</a><a href="#">Contact Us</a>
  <div class="search">Search
    <svg width="17" height="17" viewBox="0 0 17 17"><circle cx="7" cy="7" r="5" fill="none" stroke="#666" stroke-width="2"/><line x1="11" y1="11" x2="15" y2="15" stroke="#666" stroke-width="2.5"/></svg>
  </div>
</nav>

<div class="slide-arrow" style="left:32px"><svg width="10" height="12"><path d="M8 1 L2 6 L8 11Z" fill="#a0124f"/></svg></div>
<div class="slide-arrow" style="left:949px"><svg width="10" height="12"><path d="M2 1 L8 6 L2 11Z" fill="#a0124f"/></svg></div>

<div class="event">
  <div class="event-label"><strong>Current Event :</strong><span>Our video</span></div>
  <p class="event-text">There are many variations of passages of Lorem Ipsum available, but the majority have suffered alteration in some form, by injected humour, or randomised words Sed ut perspiciatis unde omnis iste natus error sit voluptatem accusantium doloremque laudantium, totam rem aperiam, eaque ipsa quae ab illo inventore veritatis et quasi architecto beatae vitae dicta sunt explicabo.</p>
  <div class="event-video" role="img" aria-label="Video still of a team meeting around a laptop">
    <svg width="42" height="42" viewBox="0 0 42 42"><circle cx="21" cy="21" r="19" fill="rgba(255,255,255,.15)" stroke="#eee" stroke-width="2"/><path d="M17 13 L29 21 L17 29Z" fill="#eee"/></svg>
  </div>
</div>

<main class="card">
  <section class="welcome">
    <h1>Welcome to Our Website</h1>
    <div class="tagline">Delivering IT Excellence</div>
    <p>Welcome to Bluefern Business Services, an emerging provider of global IT consulting and software services. We are part of the Marlow Goods group, a family run business and the world's largest multi-channel home delivery wine merchant...</p>
    <a class="btn btn-large" href="#">Read more</a>
  </section>

  <section class="services">
    <h2 class="section-title">Services</h2>
    <ul class="service-list">
      <li><svg width="14" height="12"><path d="M6 0 L0 6 L6 12Z M8 0 L14 6 L8 12Z" fill="#a0124f"/></svg>Packaged Applications</li>
      <li><svg width="14" height="12"><path d="M6 0 L0 6 L6 12Z M8 0 L14 6 L8 12Z" fill="#a0124f"/></svg>Enterprise Application Integration</li>
      <li><svg width="14" height="12"><path d="M6 0 L0 6 L6 12Z M8 0 L14 6 L8 12Z" fill="#a0124f"/></svg>Digital Commerce</li>
      <li><svg width="14" height="12"><path d="M6 0 L0 6 L6 12Z M8 0 L14 6 L8 12Z" fill="#a0124f"/></svg>Application Development &amp; Maintenance</li>
    </ul>
    <p>The services we provide enable the businesses we support to efficiently manage key functions, including order management (encompassing e&#8209;commerce websites, inbound and outbound call centre operations), order fulfilment, procurement, planning &amp; forecasting, warehouse management operations, financial management, global compliance and risk.</p>
    <a class="btn btn-small" href="#">Read more</a>
  </section>

  <div class="divider"></div>

  <section class="opportunities">
    <h2 class="section-title">Latest opportunities</h2>
    <article class="job">
      <div class="date" style="left:-27px">26<br>Nov</div>
      <div class="job-info" style="left:65px"><b>Software Developers/Programmer Analysts</b> -<p>AX We are looking for a AX Software Developer to join...<br><a href="#">read more &gt;&gt;</a></p></div>
    </article>
    <article class="job">
      <div class="date" style="left:-23px">28<br>Nov</div>
      <div class="job-info" style="left:70px"><b>Software Developers/Programmer Analysts</b> -<p>AX We are looking for a AX Software Developer to join...<br><a href="#">read more &gt;&gt;</a></p></div>
    </article>
  </section>

  <section class="clients">
    <div class="clients-title">
      <svg width="25" height="26" viewBox="0 0 25 26"><rect x="0" y="0" width="7" height="26" fill="#a8c93a"/><rect x="9" y="6" width="7" height="20" fill="#5aa0d8"/><rect x="18" y="12" width="7" height="14" fill="#f0a020"/></svg>
      OUR CLIENTS
    </div>
    <div class="client">The Coastal Cellar</div>
    <div class="client">Vinoria House</div>
    <div class="client">Oakfield Vintners</div>
    <div class="client"><i></i>Marlow Goods</div>
    <div class="client">Northgate Wines</div>
  </section>

  <nav class="footer-nav">
    <a href="#">Home</a><a href="#">About Us</a><a href="#">Clients</a><a href="#">Services</a><a href="#">Careers</a><a href="#">Contact Us</a>
  </nav>
  <p class="copyright">© 2014 Bluefern Business Services Private Limited.</p>
  <span class="version">M1</span>
</main>

<div class="social" aria-label="Social links">
  <span role="img" aria-label="Social link"></span>
  <span role="img" aria-label="Social link"></span>
  <span role="img" aria-label="News feed"></span>
  <span role="img" aria-label="Social link"></span>
</div>
</body>
</html>
```